LB - WESITE NEEDED PAGE: Clean / Modern / Pro & Dynamic

Lantern-Brokers is a new insurance brokerage firm dealing exclusively with companies (BToB) providing the following property: Liabilities Insurance Insurances Automobile Insurance Insurances Construction% 26amp; Engineering Casualty Workmen 's Compensation Health Insurance Marime% 26amp; Transit Credit Insurance Young, Fast, Proactive and Dynamic we call ourselves Lantern-Brokers because we are a "start-up" willing to make a difference in the market, bringing modernity and speed to our industry, still too bureaucratic / procedural / opaque uninitiated. We need something respecting the colors of our orange logtype; blue; white; black; easy to scroll, with simple information on the company; - who we are - our team (with the pictures) - what we do - what we do - contact us, contact us (google map) Luanda (Angola) Small company, just need something flashy / professional / structured / modern.

Target Market(s)

BtoB; Oil and gas companies; French speaking copying established in Angola, all industrials, factories and importers of goods.

Industry/Entity Type

Insurance Broker

Font styles to use
Sans Serif

Colors

Designer to choose colors to be used in the design.

Requirements
Must have
• We need something respecting the colors of our orange logtype; blue; white; black; easy to scroll, with simple information on the company; - who we are - our team (with the pictures) - what we do - what we do - contact us, contact us (google map) Luanda (Angola) Small company, just need something flashy / professional / structured / modern.
Nice to have
• A page format
Should not have
• WE DO NOT WANT A REFER TO OUR LOGO, but a Home Page for our Website with the basics categories ... >> PLEASE CAREFULLY USE THE RIGHT COLOR OF THE LOGOTYPE which are the ones enclosed Orange / Turquoise / Black as per the business card .

```html
<!DOCTYPE html>
<html lang="en">
<head>
<meta charset="utf-8">
<title>Lantern-Brokers — Insurance Brokerage</title>
<link href="https://fonts.googleapis.com/css2?family=Rubik:wght@400;500;700&family=Open+Sans:wght@400;600&display=swap" rel="stylesheet">
<style>
:root{
  --orange:#f7782b;
  --red:#f0231c;
  --red-title:#e8202a;
  --blue:#1e8ed6;
  --blue-deep:#0d5ea8;
  --ink:#1d1d1d;
  --grey:#4a4a4a;
  --white:#ffffff;
  --black:#000000;
}
*{box-sizing:border-box;margin:0;padding:0}
html,body{width:1200px;height:3563px;overflow:hidden;background:var(--white)}
body{font-family:"Open Sans",Arial,sans-serif;color:var(--ink)}
.page{position:relative;width:1200px;height:3563px;overflow:hidden}
.abs{position:absolute}

/* header */
.site-header{position:absolute;left:0;top:0;width:1200px;height:97px;background:var(--white);z-index:5}
.brand-name{position:absolute;left:158px;top:34px;font-family:"Rubik",Arial,sans-serif;font-weight:500;font-size:25px;line-height:30px;color:var(--ink)}
.main-nav a{position:absolute;top:40px;font-family:"Rubik",Arial,sans-serif;font-weight:500;font-size:15px;color:var(--grey);text-decoration:none}
.main-nav a.active{color:var(--orange)}
.nav-arc{position:absolute;left:573px;top:16px}

/* hero */
.hero{position:absolute;left:0;top:97px;width:1200px;height:620px;background:linear-gradient(90deg,#f77a2c 0%,#f8843a 40%,#f9a465 100%);overflow:hidden}
.hero-photo{position:absolute;left:480px;top:0;width:720px;height:620px;background:linear-gradient(90deg,rgba(248,132,58,0) 0%,rgba(214,150,112,.75) 20%,#c99a7d 50%,#e9ddd3 100%)}
.hero-kicker{position:absolute;left:159px;top:245px;font-family:"Rubik",Arial,sans-serif;font-weight:500;font-size:29px;color:var(--white)}
.hero-title{position:absolute;left:157px;top:282px;font-family:"Rubik",Arial,sans-serif;font-weight:700;font-size:58px;line-height:60px;color:var(--white)}
.hero-lead{position:absolute;left:159px;top:404px;font-size:18px;line-height:27px;color:var(--white)}
.slide-btn{position:absolute;width:60px;height:60px;border-radius:50%;background:rgba(255,255,255,.35);top:325px;display:flex;align-items:center;justify-content:center}

/* who we are */
.who-photo{position:absolute;left:184px;top:811px;width:332px;height:332px;border-radius:50%;background:linear-gradient(135deg,#d9d3cc,#8c6f5d 55%,#2b2d3a);box-shadow:0 6px 18px rgba(0,0,0,.2)}
.section-title{font-family:"Rubik",Arial,sans-serif;font-weight:500;font-size:33px}
.who-title{position:absolute;left:592px;top:828px;color:var(--red-title)}
.who-lead{position:absolute;left:592px;top:890px;width:500px;font-size:17px;line-height:27px;color:#333}
.who-body{position:absolute;left:592px;top:952px;width:490px;font-size:15.5px;line-height:27px;color:#555}
.btn-outline{position:absolute;left:590px;top:1081px;width:166px;height:51px;border:2px solid var(--blue);border-radius:26px;color:var(--blue);font-family:"Rubik",Arial,sans-serif;font-weight:500;font-size:16px;display:flex;align-items:center;justify-content:center}

/* team */
.team-title{position:absolute;left:0;width:1200px;top:1308px;text-align:center;color:var(--white);font-size:29px}
.member{position:absolute;top:1374px;width:200px}
.member-photo{width:190px;height:190px;border-radius:95px 95px 0 0;background:linear-gradient(160deg,#e7e2dc,#9a7a65 60%,#3d3a44)}
.member-name{margin-top:18px;font-family:"Rubik",Arial,sans-serif;font-weight:700;font-size:19px;color:var(--white)}
.member-bio{margin-top:6px;font-size:12.5px;line-height:16px;color:var(--white)}
.member-link{margin-top:6px;font-family:"Rubik",Arial,sans-serif;font-weight:700;font-size:13px;color:var(--white)}

/* services */
.services-title{position:absolute;left:0;width:1200px;top:1830px;text-align:center;color:var(--blue);font-size:33px;font-weight:700}
.service-card{position:absolute;width:401px;height:159px;border-radius:80px;background:var(--white);box-shadow:0 3px 10px rgba(0,0,0,.14);border:1px solid #e6e6e6}
.service-icon{position:absolute;top:26px;width:106px;height:106px;border-radius:50%;background:linear-gradient(135deg,#2a9ae2,#0d5ea8);display:flex;align-items:center;justify-content:center}
.service-text{position:absolute;top:38px;width:220px}
.service-card.icon-right .service-text{right:160px;text-align:right}
.service-card.icon-left .service-text{left:144px}
.service-name{font-family:"Rubik",Arial,sans-serif;font-weight:700;font-size:15px;line-height:19px;color:var(--ink)}
.service-desc{margin-top:9px;font-size:13.5px;line-height:19px;color:#555}

/* contact */
.contact-title{position:absolute;left:0;width:1200px;top:2410px;text-align:center;color:var(--white);font-size:31px}
.field{position:absolute;left:169px;width:410px;border:2px solid rgba(255,255,255,.85);background:rgba(255,255,255,.08);color:var(--white);font-size:14px;padding:12px 18px}
.btn-submit{position:absolute;left:164px;top:2748px;width:164px;height:48px;border-radius:24px;background:linear-gradient(90deg,#f0231c,#f5501e);color:var(--white);font-family:"Rubik",Arial,sans-serif;font-weight:500;font-size:17px;display:flex;align-items:center;justify-content:center}
.info-item{position:absolute;left:650px;display:flex;gap:20px;align-items:flex-start}
.info-label{font-family:"Rubik",Arial,sans-serif;font-weight:500;font-size:18px;color:var(--white)}
.info-value{font-size:17px;color:var(--white);margin-top:3px}

/* map */
.map{position:absolute;left:0;top:2873px;width:1200px;height:520px;background:linear-gradient(160deg,#e4e4e4,#cfcfcf 50%,#e9e9e9)}

/* footer */
.footer-nav{position:absolute;top:3423px;left:0;width:1200px;display:flex;justify-content:center;gap:36px}
.footer-nav a{font-family:"Rubik",Arial,sans-serif;font-weight:500;font-size:17px;color:var(--white);text-decoration:none}
.copyright{position:absolute;top:3455px;left:0;width:1200px;text-align:center;font-size:13px;color:#bbb}
.social{position:absolute;top:3496px;left:522px;display:flex;gap:7px}
.social span{width:34px;height:34px;border:1.5px solid var(--white);border-radius:50%}
</style>
</head>
<body>
<div class="page">

  <header class="site-header">
    <div class="brand-name">Lantern-Brokers</div>
    <svg class="nav-arc" width="70" height="64" viewBox="0 0 70 64"><path d="M12 22 A26 26 0 0 1 58 20" fill="none" stroke="#f7782b" stroke-width="2.5"/><path d="M14 44 A26 26 0 0 0 56 46" fill="none" stroke="#f7782b" stroke-width="2.5"/></svg>
    <nav class="main-nav">
      <a class="active" style="left:571px">ABOUT US</a>
      <a style="left:675px">SERVICES</a>
      <a style="left:776px">BLOGS</a>
      <a style="left:854px">TESTIMONIAL</a>
      <a style="left:981px">CONTACT US</a>
    </nav>
  </header>

  <section class="hero">
    <div class="hero-photo" role="img" aria-label="Photo of a smiling family sitting together on a sofa"></div>
    <div class="hero-kicker">WELCOME TO</div>
    <h1 class="hero-title">LANTERN<br>BROKERS</h1>
    <p class="hero-lead">Lorem ipsum dolor sit amet consectetuer<br>adipiscing elit Nam cursus Morbi</p>
    <div class="slide-btn" style="left:64px"><svg width="16" height="24" viewBox="0 0 16 24"><path d="M12 3 L4 12 L12 21" fill="none" stroke="#222" stroke-width="3"/></svg></div>
    <div class="slide-btn" style="left:1059px"><svg width="16" height="24" viewBox="0 0 16 24"><path d="M4 3 L12 12 L4 21" fill="none" stroke="#222" stroke-width="3"/></svg></div>
  </section>
  <svg class="abs" style="left:0;top:560px" width="1200" height="180" viewBox="0 560 1200 180">
    <path d="M0 594 Q600 775 1200 594 L1200 740 L0 740 Z" fill="#fff"/>
    <path d="M0 605 Q600 805 1200 605" fill="none" stroke="#f7782b" stroke-width="4"/>
  </svg>

  <!-- who we are -->
  <svg class="abs" style="left:160px;top:787px" width="380" height="380" viewBox="0 0 380 380">
    <path d="M190 3 A187 187 0 1 1 30 95" fill="none" stroke="#1e8ed6" stroke-width="16" transform="rotate(-80 190 190)"/>
  </svg>
  <div class="who-photo" role="img" aria-label="Photo of two smiling business colleagues"></div>
  <h2 class="section-title who-title">WHO WE ARE</h2>
  <p class="who-lead">Pellentesque faucibus Ut accumsan ultricies elit Maecenas at justo id velit placerat molestie Donec dictum</p>
  <p class="who-body">Cras a ante vitae enim iaculis aliquam Mauris nunc &nbsp;est nunc venenatis in tristique eu imperdiet ac nisl Cum sociis natoque penatibus et magnis dis parturient montes nascetur ridiculus mus In iaculis facilisis massa Etiam eu urna Sed porta</p>
  <div class="btn-outline">LEARN MORE</div>

  <!-- team band -->
  <svg class="abs" style="left:0;top:1170px" width="1200" height="670" viewBox="0 1170 1200 670">
    <defs>
      <linearGradient id="teamGrad" x1="0" y1="0" x2="1" y2="1">
        <stop offset="0" stop-color="#f41c1c"/>
        <stop offset="1" stop-color="#f7782b"/>
      </linearGradient>
      <linearGradient id="blueLine" x1="0" x2="1">
        <stop offset="0" stop-color="#1e8ed6" stop-opacity="0"/>
        <stop offset=".2" stop-color="#1e8ed6"/>
        <stop offset=".8" stop-color="#1e8ed6"/>
        <stop offset="1" stop-color="#1e8ed6" stop-opacity="0"/>
      </linearGradient>
    </defs>
    <path d="M0 1175 Q600 1327 1200 1175 L1200 1840 L0 1840 Z" fill="url(#teamGrad)"/>
    <path d="M0 1834 Q600 1690 1200 1834 L1200 1840 L0 1840 Z" fill="#fff"/>
    <path d="M60 1815 Q600 1690 1140 1815" fill="none" stroke="url(#blueLine)" stroke-width="4"/>
  </svg>
  <h2 class="section-title team-title">OUR TEAM</h2>
  <svg class="abs" style="left:103px;top:1490px" width="30" height="56" viewBox="0 0 30 56"><path d="M26 2 L4 28 L26 54" fill="none" stroke="#fff" stroke-width="2"/></svg>
  <svg class="abs" style="left:1067px;top:1490px" width="30" height="56" viewBox="0 0 30 56"><path d="M4 2 L26 28 L4 54" fill="none" stroke="#fff" stroke-width="2"/></svg>
  <div class="member" style="left:169px"><div class="member-photo" role="img" aria-label="Portrait of a team member in a blue shirt"></div><div class="member-name">Member Name</div><div class="member-bio">sociosqu ad litora torquent<br>per conubia sociosqu</div><div class="member-link">LEARN MORE</div></div>
  <div class="member" style="left:401px"><div class="member-photo" role="img" aria-label="Portrait of a team member in a suit"></div><div class="member-name">Member Name</div><div class="member-bio">sociosqu ad litora torquent<br>per conubia sociosqu</div><div class="member-link">LEARN MORE</div></div>
  <div class="member" style="left:633px"><div class="member-photo" role="img" aria-label="Portrait of a team member holding glasses"></div><div class="member-name">Member Name</div><div class="member-bio">sociosqu ad litora torquent<br>per conubia sociosqu</div><div class="member-link">LEARN MORE</div></div>
  <div class="member" style="left:865px"><div class="member-photo" role="img" aria-label="Portrait of a team member in a grey blazer"></div><div class="member-name">Member Name</div><div class="member-bio">sociosqu ad litora torquent<br>per conubia sociosqu</div><div class="member-link">LEARN MORE</div></div>

  <!-- what we do -->
  <h2 class="section-title services-title">WHAT WE DO</h2>
  <div class="service-card icon-right" style="left:182px;top:1908px">
    <div class="service-text"><div class="service-name">Liabilities Insurance<br>Insurances</div><div class="service-desc">Aolor ultrices ipsum dictum<br>tristique Praesent vitae lacus Ut</div></div>
    <div class="service-icon" style="left:260px"><svg width="50" height="50" viewBox="0 0 50 50" fill="none" stroke="#fff" stroke-width="2"><path d="M8 22 A17 17 0 0 1 42 22 Z"/><path d="M25 22 V30"/><path d="M6 40 H16 L26 44 L42 36 L38 33 L28 37 H20"/></svg></div>
  </div>
  <div class="service-card icon-left" style="left:611px;top:1908px">
    <div class="service-icon" style="left:26px"><svg width="50" height="50" viewBox="0 0 50 50" fill="none" stroke="#fff" stroke-width="2"><rect x="10" y="14" width="30" height="26" rx="3"/><path d="M19 14 V9 H31 V14"/><path d="M25 20 V34 M18 27 H32"/></svg></div>
    <div class="service-text"><div class="service-name">Compensation Health<br>Insurance</div><div class="service-desc">Dolor ultrices ipsum dictum<br>tristique Praesent vitae lacus Ut</div></div>
  </div>
  <div class="service-card icon-right" style="left:187px;top:2085px">
    <div class="service-text"><div class="service-name">Automobile Insurance<br>Insurances</div><div class="service-desc">Dolor ultrices ipsum dictum<br>tristique Praesent vitae lacus Ut</div></div>
    <div class="service-icon" style="left:260px"><svg width="64" height="40" viewBox="0 0 64 40" fill="none" stroke="#fff" stroke-width="2"><path d="M4 28 V22 L12 18 L22 10 H42 L52 18 L60 21 V28 Z"/><circle cx="18" cy="29" r="5"/><circle cx="47" cy="29" r="5"/></svg></div>
  </div>
  <div class="service-card icon-left" style="left:615px;top:2085px">
    <div class="service-icon" style="left:26px"><svg width="50" height="54" viewBox="0 0 50 54" fill="none" stroke="#fff" stroke-width="2"><path d="M12 20 A13 13 0 0 1 38 20 Z"/><path d="M8 20 H42"/><path d="M16 22 A9 10 0 0 0 34 22"/><path d="M6 50 A19 14 0 0 1 44 50 Z"/></svg></div>
    <div class="service-text"><div class="service-name">Construction &amp; Engineering<br>Casualty Workmen 's</div><div class="service-desc">Dolor ultrices ipsum dictum<br>tristique Praesent vitae lacus Ut</div></div>
  </div>

  <!-- contact band -->
  <svg class="abs" style="left:0;top:2275px" width="1200" height="600" viewBox="0 2275 1200 600">
    <defs>
      <linearGradient id="contactGrad" x1="0" y1="0" x2="1" y2="1">
        <stop offset="0" stop-color="#2596dc"/>
        <stop offset="1" stop-color="#0d5ea8"/>
      </linearGradient>
      <linearGradient id="orangeLine" x1="0" x2="1">
        <stop offset="0" stop-color="#f7782b" stop-opacity="0"/>
        <stop offset=".2" stop-color="#f7782b"/>
        <stop offset=".8" stop-color="#f7782b"/>
        <stop offset="1" stop-color="#f7782b" stop-opacity="0"/>
      </linearGradient>
    </defs>
    <path d="M0 2281 Q600 2420 1200 2281 L1200 2875 L0 2875 Z" fill="url(#contactGrad)"/>
    <path d="M90 2296 Q600 2398 1110 2296" fill="none" stroke="url(#orangeLine)" stroke-width="4"/>
  </svg>
  <h2 class="section-title contact-title">CONTACT US</h2>
  <div class="field" style="top:2500px;height:45px">Name</div>
  <div class="field" style="top:2553px;height:45px">Email address</div>
  <div class="field" style="top:2605px;height:45px">Phone</div>
  <div class="field" style="top:2658px;height:75px">Message</div>
  <div class="btn-submit">SUBMIT</div>

  <div class="info-item" style="top:2497px">
    <svg width="42" height="44" viewBox="0 0 42 44" fill="none" stroke="#fff" stroke-width="1.8"><path d="M21 30 C12 20 10 16 10 12 A11 11 0 0 1 32 12 C32 16 30 20 21 30 Z"/><circle cx="21" cy="12" r="4"/><ellipse cx="21" cy="36" rx="19" ry="6"/></svg>
    <div><div class="info-label">ADDRESS</div><div class="info-value">48 Rua das Acácias, Ingombota, Luanda</div></div>
  </div>
  <div class="info-item" style="top:2578px">
    <svg width="42" height="44" viewBox="0 0 42 44" fill="none" stroke="#fff" stroke-width="1.8"><path d="M8 4 L15 4 L19 13 L14 17 C17 24 21 28 27 31 L31 26 L40 30 L40 37 C40 40 37 42 34 41 C18 37 7 26 3 10 C2 7 5 4 8 4 Z"/></svg>
    <div><div class="info-label">PHONE</div><div class="info-value">+244 923 410 785</div></div>
  </div>
  <div class="info-item" style="top:2660px">
    <svg width="42" height="40" viewBox="0 0 42 40" fill="none" stroke="#fff" stroke-width="1.8"><rect x="2" y="8" width="38" height="26"/><path d="M2 8 L21 24 L40 8 M2 34 L16 20 M40 34 L26 20"/></svg>
    <div><div class="info-label">EMAIL US</div><div class="info-value">hello@lanternbrokers.co.ao</div></div>
  </div>

  <div class="map" role="img" aria-label="Street map of central Luanda with a location pin on the office"></div>

  <!-- footer -->
  <svg class="abs" style="left:0;top:3290px" width="1200" height="273" viewBox="0 3290 1200 273">
    <path d="M0 3290 Q600 3440 1200 3290 L1200 3563 L0 3563 Z" fill="#f7782b"/>
    <path d="M0 3300 Q600 3445 1200 3300 L1200 3563 L0 3563 Z" fill="#000"/>
  </svg>
  <nav class="footer-nav">
    <a>ABOUT US</a><a>SERVICES</a><a>BLOGS</a><a>TESTIMONIAL</a><a>CONTACT US</a>
  </nav>
  <div class="copyright">© 2019 Company Name &nbsp;All right reserved</div>
  <div class="social" aria-label="Social links"><span></span><span></span><span></span><span></span></div>

</div>
</body>
</html>
```